Brintel Works - Fast, Efficient and Gas Mainteance for Domestic, Commercial and Industrial clients

We are in the process of purchasing a new business and would like to get a new logo and business card.
Business is a gas maintenance business that also does new gas installations.
Has been established since 1988.
Services include:
Install all types of gas appliances & equipment inc. hot water units
Maintain / repair / replace all types of gas appliances & equipment

Target Market(s)

Domestic, Commercial and Industrial clients

Industry/Entity Type

Business

Contact Information for Business Card

admin@brintelworks.com.au
07 3918 4726
Brintel Works PTY LTD

Logo Text

Gas Fitting & Plumbing Maintenance Specialists

Font styles to use
Sans Serif

Requirements
Must have
• Logo
• Business name, contact number, email address, web address
• Domestic | Commercial | Industrial Est Since 1988
Nice to have
• Possibly a black card with a flame logo to one side
Should not have
• Spelling errors

```html
<!DOCTYPE html>
<html lang="en">
<head>
<meta charset="utf-8">
<title>Brintel Works – Business Card</title>
<link href="https://fonts.googleapis.com/css2?family=PT+Serif&family=Ubuntu:wght@400;500&family=Arimo&family=Dancing+Script&display=swap" rel="stylesheet">
<style>
  :root {
    --page-bg: #e9e6e1;
    --card-bg: #ffffff;
    --card-shade: #f1f1f1;
    --brand-orange: #e4673f;
    --ink-dark: #3d3f45;
    --ink-body: #222222;
    --ink-muted: #7b7e84;
    --logo-panel: #ececec;
  }
  html, body {
    margin: 0;
    width: 1200px;
    height: 892px;
    overflow: hidden;
    background: var(--page-bg);
  }
  .card {
    position: absolute;
    left: 100px;
    top: 168px;
    width: 1000px;
    height: 556px;
    background: linear-gradient(135deg, var(--card-bg) 55%, var(--card-shade));
    box-shadow: 0 10px 30px rgba(0,0,0,0.18);
  }
  .logo-panel {
    position: absolute;
    left: 40px;
    top: 70px;
    width: 560px;
    height: 210px;
    background: linear-gradient(90deg, var(--logo-panel), #f7f7f7);
  }
  .brand-name {
    position: absolute;
    left: 140px;
    top: 78px;
    margin: 0;
    font-family: "PT Serif", serif;
    font-weight: 400;
    font-size: 44px;
    letter-spacing: 1px;
    color: var(--brand-orange);
    text-transform: uppercase;
  }
  .brand-suffix {
    position: absolute;
    left: 530px;
    top: 82px;
    font-family: "Ubuntu", sans-serif;
    font-size: 9px;
    font-weight: 500;
    color: var(--ink-dark);
  }
  .tagline {
    position: absolute;
    left: 140px;
    top: 140px;
    margin: 0;
    font-family: "Ubuntu", sans-serif;
    font-weight: 500;
    font-size: 27px;
    color: var(--ink-dark);
  }
  .sectors {
    position: absolute;
    left: 140px;
    top: 186px;
    font-family: "Ubuntu", sans-serif;
    font-size: 14px;
    color: var(--ink-muted);
  }
  .established {
    position: absolute;
    left: 420px;
    top: 172px;
    font-family: "Dancing Script", cursive;
    font-size: 30px;
    color: var(--ink-muted);
  }
  .product-visual {
    position: absolute;
    left: 640px;
    top: 30px;
    width: 320px;
    height: 300px;
    background: radial-gradient(circle at 40% 60%, #d9582a 0 18%, #8c8f93 19% 55%, #c7c9cc 56%);
    border-radius: 6px;
  }
  .contact-list {
    position: absolute;
    left: 40px;
    top: 330px;
    margin: 0;
    padding: 0;
    list-style: none;
    font-family: "Arimo", sans-serif;
    font-size: 27px;
    color: var(--ink-body);
  }
  .contact-list li {
    display: flex;
    align-items: center;
    height: 38px;
  }
  .contact-icon {
    width: 20px;
    height: 20px;
    margin-right: 22px;
    flex: none;
  }
</style>
</head>
<body>
  <div class="card">
    <div class="logo-panel"></div>
    <h1 class="brand-name">Brintel Works</h1>
    <span class="brand-suffix">PTY LTD</span>
    <p class="tagline">Gas fitting &amp; Plumbing Specialists</p>
    <span class="sectors">Domestic | Commercial | Industrial</span>
    <span class="established">Est Since 1988</span>

    <div class="product-visual" role="img" aria-label="Product photo of gas hot water units and a gas log fireplace"></div>

    <ul class="contact-list">
      <li>
        <svg class="contact-icon" viewBox="0 0 20 20"><rect width="20" height="20" fill="#e4673f"/><path d="M6 4l2 3-1.5 1.5a7 7 0 0 0 5 5L13 12l3 2-1 2c-5 0-10-5-10-10z" fill="#fff"/></svg>
        07 3918 4726
      </li>
      <li>
        <svg class="contact-icon" viewBox="0 0 20 20"><rect width="20" height="20" fill="#e4673f"/><rect x="5" y="7" width="10" height="8" fill="#fff"/><rect x="7" y="4" width="6" height="4" fill="#fff"/><rect x="7" y="9" width="6" height="1.5" fill="#e4673f"/></svg>
        07 3918 4739
      </li>
      <li>
        <svg class="contact-icon" viewBox="0 0 20 20"><rect width="20" height="20" fill="#e4673f"/><circle cx="10" cy="10" r="5.5" fill="none" stroke="#fff" stroke-width="1.5"/><path d="M4.5 10h11M10 4.5v11" stroke="#fff" stroke-width="1.2"/></svg>
        www.brintelworks.com.au
      </li>
      <li>
        <svg class="contact-icon" viewBox="0 0 20 20"><rect width="20" height="20" fill="#e4673f"/><rect x="4" y="6" width="12" height="8" fill="#fff"/><path d="M4 6l6 5 6-5" fill="none" stroke="#e4673f" stroke-width="1.3"/></svg>
        admin@brintelworks.com.au
      </li>
      <li>
        <svg class="contact-icon" viewBox="0 0 20 20"><rect width="20" height="20" fill="#e4673f"/><path d="M10 16s-4.5-5-4.5-8a4.5 4.5 0 0 1 9 0c0 3-4.5 8-4.5 8z" fill="#fff"/><circle cx="10" cy="8" r="1.6" fill="#e4673f"/></svg>
        PO Box 2864, Larkin Heads, QLD 4230
      </li>
    </ul>
  </div>
</body>
</html>
```